Harborline Renewal Business Card Design

Professional and clean design. The design colors should flow with the logo. Two-sided card with the website on the back which is:

www.HarborlineRenewal.example.

"Specializing in Water Damage Restoration"

On the front I need the name, email, phone, and logo.

Name: Darnell Quisby
Email: Darnell@HarborlineRenewal.example
Phone: 555-318-2046 for now

I only have the Preview and Thumbnail right now but should have the source files uploaded within a day or two.

Target Market(s)

Flood victims, home owners with water damage from busted pipes etc...

Industry/Entity Type

Business

Contact Information for Business Card

Name: Darnell Quisby

Font styles to use
Serif
Sans Serif

Requirements
Must have
• Business Card Details Info

```html
<!DOCTYPE html>
<html lang="en">
<head>
<meta charset="utf-8">
<title>Harborline Renewal Business Card</title>
<link rel="stylesheet" href="https://fonts.googleapis.com/css2?family=Cinzel:wght@500&family=Open+Sans:wght@400;600&display=swap">
<style>
  :root {
    --stage-top: #2a2a2a;
    --stage-bottom: #050505;
    --card-light: #f3f3f3;
    --brand-blue: #2a9ad6;
    --back-blue-top: #2597d3;
    --back-blue-bottom: #1d86c6;
    --ink: #222222;
    --white: #ffffff;
  }
  * { margin: 0; padding: 0; box-sizing: border-box; }
  html, body { width: 1200px; height: 900px; overflow: hidden; }
  body {
    position: relative;
    background: linear-gradient(180deg, var(--stage-top) 0%, #151515 55%, var(--stage-bottom) 100%);
    font-family: "Open Sans", Arial, sans-serif;
  }
  .card {
    position: absolute;
    top: 184px;
    width: 302px;
    height: 490px;
    border-radius: 12px;
    overflow: hidden;
    text-align: center;
  }
  .card-front { left: 299px; background: var(--card-light); }
  .card-back {
    left: 645px;
    width: 304px;
    background: linear-gradient(180deg, var(--back-blue-top) 0%, var(--back-blue-bottom) 100%);
    color: var(--white);
  }
  .brand-dot {
    position: absolute;
    left: 50%;
    top: 39px;
    width: 68px;
    height: 68px;
    margin-left: -34px;
    border-radius: 50%;
    background: var(--brand-blue);
  }
  .brand-name {
    position: absolute;
    left: 0; right: 0;
    font-family: "Cinzel", Georgia, serif;
    font-weight: 500;
    letter-spacing: 0.5px;
    white-space: nowrap;
  }
  .card-front .brand-name { top: 120px; font-size: 22px; color: var(--brand-blue); }
  .card-back .brand-name { top: 330px; font-size: 23px; color: var(--white); }
  .back-circle {
    position: absolute;
    left: -40px;
    top: -120px;
    width: 390px;
    height: 390px;
    border-radius: 50%;
    background: rgba(255,255,255,0.04);
  }
  .person-name {
    position: absolute;
    left: 0; right: 0;
    top: 364px;
    font-size: 18px;
    font-weight: 600;
    color: var(--brand-blue);
  }
  .contact-line {
    position: absolute;
    left: 0; right: 0;
    font-size: 12.5px;
    color: var(--ink);
    display: flex;
    justify-content: center;
    align-items: center;
    gap: 5px;
  }
  .contact-phone { top: 409px; }
  .contact-email { top: 429px; }
  .contact-line svg { fill: var(--brand-blue); }
  .website {
    position: absolute;
    left: 0; right: 0;
    top: 402px;
    font-size: 13px;
    font-weight: 600;
  }
  .tagline {
    position: absolute;
    left: 0; right: 0;
    top: 439px;
    font-size: 14.5px;
    font-weight: 600;
    white-space: nowrap;
  }
</style>
</head>
<body>
  <section class="card card-front" aria-label="Card front">
    <div class="brand-dot"></div>
    <div class="brand-name">Harborline Renewal</div>
    <div class="person-name">Darnell Quisby</div>
    <div class="contact-line contact-phone">
      <svg width="10" height="10" viewBox="0 0 24 24" aria-hidden="true"><path d="M6.6 10.8c1.4 2.8 3.8 5.1 6.6 6.6l2.2-2.2c.3-.3.7-.4 1-.2 1.1.4 2.3.6 3.6.6.6 0 1 .4 1 1V20c0 .6-.4 1-1 1C10.6 21 3 13.4 3 4c0-.6.4-1 1-1h3.5c.6 0 1 .4 1 1 0 1.3.2 2.5.6 3.6.1.3 0 .7-.2 1L6.6 10.8z"/></svg>
      <span>555-318-2046</span>
    </div>
    <div class="contact-line contact-email">
      <svg width="11" height="9" viewBox="0 0 24 18" aria-hidden="true"><path d="M0 0h24v18H0z M2 2v.6l10 6.6 10-6.6V2z" fill-rule="evenodd"/></svg>
      <span>Darnell@HarborlineRenewal.example</span>
    </div>
  </section>

  <section class="card card-back" aria-label="Card back">
    <div class="back-circle"></div>
    <div class="brand-name">Harborline Renewal</div>
    <div class="website">www.HarborlineRenewal.example</div>
    <div class="tagline">Specializing in Water Damage Restoration</div>
  </section>
</body>
</html>
```